Jolly Hounds Dog Behaviour, Training and Natural Healthcare Business Card Design

I am an experienced and qualified dog behavioural trainer and natural animal healthcare consultant offering a range of services to help pet dog owners with the "whole dog".
COLOURS: A soft light blue in the background - can be fading out or split, red should also feature
LOGO: Dog, healing hands, silhouette, shadow
SERVICES: Behaviour Consults, Training, Complex Skills Coaching Walking Coaching, Diet & Nutrition, Environmental Enrichment, Lifestyle and Lifestage Adaptations, Massage, Natural Health Options
BY LINE: Happy Dogs, Happy Owners
VALUES: Promoting communication and connection between dogs and their owners.
FOCUS: Nutritional guidance and environmental adaptation are often needed to complete the package and increase the success rate of training and behaviour modification.

Target Market(s)

Everyone who has a dog who they wish to improve their relationship with

Industry/Entity Type

Communication

Contact Information for Business Card

Jolly Hounds, Rebecca Thornbury, 0427 861350, jollyhounds7@fernpost.example, www.jollyhounds7.example, Qualified Dog Behavioural Trainer and Natural Animal Healthcare Consultant

Font styles to use
Sans Serif
Script

Colors
85cae6
ec2027

Requirements
Must have
• A clear indication that it is a dog services business. A raised feature
Should not have
• Pawprints, cartoons

```html
<!DOCTYPE html>
<html lang="en">
<head>
<meta charset="utf-8">
<title>Jolly Hounds Business Card</title>
<link href="https://fonts.googleapis.com/css2?family=Baloo+2:wght@800&family=Courier+Prime&family=Open+Sans:wght@400;600&display=swap" rel="stylesheet">
<style>
  :root {
    --stage: #1c1c1c;
    --card-white: #ffffff;
    --sky-blue: #85cae6;
    --brand-red: #ec2027;
    --ink: #111111;
    --photo-top: #a9c8ec;
    --photo-mid: #c9d7e6;
    --photo-fur: #bfa98c;
    --photo-green: #5f8a3a;
  }
  html, body {
    margin: 0;
    padding: 0;
    width: 1200px;
    height: 900px;
    overflow: hidden;
    background: var(--stage);
  }
  .business-card {
    position: absolute;
    left: 100px;
    top: 160px;
    width: 1000px;
    height: 580px;
    background: var(--card-white);
    overflow: hidden;
    box-shadow: 0 12px 30px rgba(0,0,0,0.5);
  }
  .card-art {
    position: absolute;
    inset: 0;
    width: 1000px;
    height: 580px;
  }
  .brand-name {
    position: absolute;
    left: 380px;
    top: 4px;
    margin: 0;
    font-family: "Baloo 2", sans-serif;
    font-weight: 800;
    font-size: 70px;
    line-height: 1;
    color: var(--brand-red);
  }
  .tagline {
    position: absolute;
    top: 82px;
    left: 200px;
    width: 690px;
    margin: 0;
    font-family: "Courier Prime", monospace;
    font-size: 21px;
    line-height: 1.15;
    color: var(--brand-red);
  }
  .tagline-line { display: block; }
  .tagline-line.first { padding-left: 200px; }
  .contact-person {
    position: absolute;
    right: 60px;
    top: 360px;
    text-align: left;
    font-family: "Open Sans", sans-serif;
    color: var(--ink);
  }
  .person-name {
    margin: 0;
    font-size: 42px;
    font-weight: 400;
    line-height: 1.1;
  }
  .person-phone {
    margin: 0 0 0 18px;
    font-size: 32px;
    font-weight: 600;
    letter-spacing: 1px;
  }
  .contact-line {
    position: absolute;
    display: flex;
    align-items: center;
    gap: 14px;
    font-family: "Open Sans", sans-serif;
    font-weight: 600;
    font-size: 26px;
    color: var(--ink);
  }
  .contact-line svg { width: 22px; height: 22px; flex: none; }
  .contact-email { left: 50px; top: 390px; }
  .contact-web { left: 360px; top: 500px; }
</style>
</head>
<body>
  <section class="business-card">
    <svg class="card-art" viewBox="0 0 1000 580" xmlns="http://www.w3.org/2000/svg">
      <defs>
        <linearGradient id="photoTone" x1="0" y1="0" x2="1" y2="1">
          <stop offset="0" stop-color="var(--photo-top)"/>
          <stop offset="0.45" stop-color="var(--photo-mid)"/>
          <stop offset="0.7" stop-color="var(--photo-fur)"/>
          <stop offset="1" stop-color="var(--photo-top)"/>
        </linearGradient>
      </defs>
      <g role="img" aria-label="Photo of a happy fluffy puppy against a blue sky with a green tree">
        <path d="M0 0 H1000 V70 C820 190 520 290 0 318 Z" fill="url(#photoTone)"/>
      </g>
      <path class="swoosh-red" d="M0 334 C520 306 820 210 1000 92 V258 C800 300 500 328 0 342 Z" fill="var(--brand-red)"/>
      <path class="swoosh-line" d="M0 326 C520 296 820 198 1000 80" fill="none" stroke="var(--brand-red)" stroke-width="2"/>
      <path class="panel-blue" d="M0 352 C500 340 800 306 1000 270 V580 H0 Z" fill="var(--sky-blue)"/>
    </svg>

    <h1 class="brand-name">Jolly Hounds</h1>
    <p class="tagline">
      <span class="tagline-line first">Qualified Dog Behavioural</span>
      <span class="tagline-line">Trainer and Natural Animal Healthcare Consultant</span>
    </p>

    <div class="contact-person">
      <p class="person-name">Rebecca Thornbury</p>
      <p class="person-phone">0427 861350</p>
    </div>

    <div class="contact-line contact-email">
      <svg viewBox="0 0 24 24" aria-hidden="true"><rect x="2" y="5" width="20" height="14" rx="2" fill="var(--ink)"/><path d="M3 6 L12 13 L21 6" fill="none" stroke="var(--sky-blue)" stroke-width="2"/></svg>
      <span>jollyhounds7@fernpost.example</span>
    </div>
    <div class="contact-line contact-web">
      <svg viewBox="0 0 24 24" aria-hidden="true"><circle cx="12" cy="12" r="10" fill="none" stroke="var(--ink)" stroke-width="2"/><ellipse cx="12" cy="12" rx="4" ry="10" fill="none" stroke="var(--ink)" stroke-width="1.5"/><path d="M2 12 H22 M4 7 H20 M4 17 H20" stroke="var(--ink)" stroke-width="1.5"/></svg>
      <span>www.jollyhounds7.example</span>
    </div>
  </section>
</body>
</html>
```